Retail/Wholesale website graphic template

I need to design a new graphic template for a website for a client. The website will be a retail/wholesale company site with most pages dedicated to presentation. There will also be an online store and a blog. However, you don't need to worry about those. All I need from you is a graphic template for a generic site page.

It will need to include standard UI elements, in case I need those. I am attaching a more detailed assignment in .docx format.

The logo is also attached.

Target Market(s)

small business owners, (occasional) retail customers

Industry/Entity Type

Wholesale

Number of Pages Required

1 page

Font styles to use
Serif
Sans Serif

Colors
ec1f27
474747

Requirements
Must have
• must match logo, be clean, minimal and with slightly larger text size
Should not have
• must not be modern-looking where you have to scroll and scroll and scroll to get to the bottom of the homepage. most of my visitors are "old" people, they do not get this type of design.

```html
<!DOCTYPE html>
<html lang="en">
<head>
<meta charset="utf-8">
<title>Quillmere Imports</title>
<link href="https://fonts.googleapis.com/css2?family=Open+Sans:wght@400;600;700&display=swap" rel="stylesheet">
<style>
:root{
  --red:#e2001a;
  --dark:#333333;
  --charcoal:#474747;
  --text:#444444;
  --muted:#666666;
  --light:#f0f0f0;
  --white:#ffffff;
  --line:#cfcfcf;
  --footer-text:#a8a8a8;
}
*{box-sizing:border-box;margin:0;padding:0}
html,body{width:1200px;height:2932px;overflow:hidden}
body{font-family:"Open Sans",Arial,sans-serif;color:var(--text);background:var(--white);position:relative}
section,header,footer,.topbar{position:absolute;left:0;width:1200px}
.btn{position:absolute;background:var(--red);color:var(--white);font-size:13px;font-weight:600;display:flex;align-items:center;justify-content:center;text-transform:uppercase;letter-spacing:.2px}
.section-title{position:absolute;left:0;width:1200px;text-align:center;font-weight:700;font-size:32px;color:var(--red);text-transform:uppercase}

/* top bar */
.topbar{top:0;height:39px;background:var(--dark);color:#ddd;font-size:11px}
.topbar .item{position:absolute;top:13px;display:flex;align-items:center;gap:6px}

/* header */
.site-header{top:39px;height:104px;background:var(--white)}
.brand{position:absolute;left:133px;top:36px;font-size:21px;font-weight:700;color:var(--red);letter-spacing:.5px;display:flex;align-items:center;gap:8px;white-space:nowrap}
.brand .mark{width:13px;height:13px;background:var(--red)}
.nav a{position:absolute;top:44px;font-size:13px;color:#222;text-decoration:none}
.nav a.active{color:var(--red)}
.dropdown{position:absolute;left:733px;top:65px;width:92px;height:78px;background:var(--red);padding:4px 0;z-index:3}
.dropdown span{display:block;color:var(--white);font-size:11px;padding:3px 12px;height:26px;line-height:20px}

/* hero */
.hero{top:143px;height:472px;background:linear-gradient(180deg,#2f3845 0%,#7a6150 38%,#3d4a5d 70%,#25324a 100%)}
.hero h1{position:absolute;top:157px;left:0;width:1200px;text-align:center;color:var(--white);font-size:40px;line-height:45px;font-weight:700;text-transform:uppercase}
.hero .arrow{position:absolute;top:220px}

/* welcome */
.welcome{top:615px;height:464px}
.welcome p.lead{position:absolute;left:133px;top:118px;width:934px;text-align:center;font-size:12.8px;line-height:23.5px;color:var(--muted)}
.bullets{position:absolute;top:207px;list-style:none;font-size:14.6px;color:#222;white-space:nowrap}
.bullets li{height:27.4px;padding-left:14px;position:relative}
.bullets li::before{content:"";position:absolute;left:0;top:9px;width:5px;height:5px;border-radius:50%;background:#222}

/* services */
.services{top:1079px;height:510px;background:linear-gradient(135deg,#2b2b2b 0%,#4a4a4a 45%,#303030 100%)}
.services .section-title{color:var(--white);top:86px;font-size:31px}
.service-card{position:absolute;top:154px;width:299px;height:238px;border:2px solid rgba(255,255,255,.85);text-align:center;color:var(--white)}
.service-card svg{position:absolute;left:107px;top:25px}
.service-card h3{position:absolute;top:96px;width:100%;font-size:22px;font-weight:700;text-transform:uppercase}
.service-card p{position:absolute;top:142px;left:30px;width:235px;font-size:11px;line-height:15px;color:#ddd}
.service-card .btn{left:94px;top:215px;width:106px;height:41px}

/* case studies */
.cases{top:1589px;height:604px}
.case{position:absolute;top:131px;width:299px}
.case .photo{height:214px}
.case h4{margin-top:12px;font-size:15.5px;font-weight:400;color:#111;line-height:23px}
.case p{margin-top:8px;font-size:10.5px;line-height:18px;color:#333}
.case .btn{position:static;margin-top:14px;width:105px;height:41px}
.cases .arrow{position:absolute;top:225px}

/* contact */
.contact{top:2193px;height:380px;background:var(--light)}
.field{position:absolute;height:39px;background:var(--white);border:1px solid var(--line);font-size:11px;color:#999;padding:0 12px;display:flex;align-items:center}

/* footer */
.site-footer{top:2573px;height:359px;background:var(--dark);color:var(--footer-text)}
.footer-brand{position:absolute;left:133px;top:48px;font-size:21px;font-weight:700;color:#bbbbbb;letter-spacing:.5px}
.fcol{position:absolute;top:124px;font-size:11px;line-height:19px}
.fcol h5{font-size:12.5px;font-weight:400;color:var(--white);margin-bottom:6px}
.footer-rule{position:absolute;left:133px;top:274px;width:934px;height:1px;background:#4d4d4d}
.legal{position:absolute;left:133px;top:307px;font-size:10.5px}
.social{position:absolute;top:306px;display:flex;gap:26px;left:940px}
.social span{width:13px;height:13px;border-radius:50%;background:#bbbbbb;display:block}
</style>
</head>
<body>

<div class="topbar">
  <div class="item" style="left:752px">
    <svg width="10" height="10" viewBox="0 0 10 10"><path d="M2 1l2 2-1 1.2c.6 1.2 1.6 2.2 2.8 2.8L7 6l2 2-1.2 1.3C4.5 9 1 5.5.7 2.2z" fill="#ddd"/></svg>555 210 4387</div>
  <div class="item" style="left:866px">
    <svg width="11" height="9" viewBox="0 0 11 9"><rect x=".5" y=".5" width="10" height="8" fill="#ddd"/><path d="M.5 .8l5 4 5-4" stroke="#333" fill="none"/></svg>info@quillmereimports.com</div>
  <div class="item" style="left:1035px">
    <svg width="10" height="10" viewBox="0 0 10 10"><path d="M4 1h5v8H4M1 5h5M4 3l2 2-2 2" stroke="#ddd" fill="none" stroke-width="1.3"/></svg>Login</div>
</div>

<header class="site-header">
  <div class="brand"><span class="mark"></span>QUILLMERE IMPORTS</div>
  <nav class="nav">
    <a style="left:668px">Home</a>
    <a class="active" style="left:733px">About Us ▾</a>
    <a style="left:820px">Services ▾</a>
    <a style="left:905px">Case Studies</a>
    <a style="left:1006px">Contact Us</a>
  </nav>
  <div class="dropdown"><span>• Our History</span><span>• Our Team</span><span>• Why Us?</span></div>
</header>

<section class="hero" role="img" aria-label="Photo of a truck at a cargo port with container stacks, a crane and a plane in an evening sky">
  <h1>Vestibulum condimentum<br>risus posuere cursus</h1>
  <div class="btn" style="left:547px;top:261px;width:106px;height:42px">Read more</div>
  <svg class="arrow" style="left:46px" width="18" height="30" viewBox="0 0 18 30"><path d="M15 3L4 15l11 12" stroke="#fff" stroke-width="4" fill="none"/></svg>
  <svg class="arrow" style="left:1134px" width="18" height="30" viewBox="0 0 18 30"><path d="M3 3l11 12L3 27" stroke="#fff" stroke-width="4" fill="none"/></svg>
</section>

<section class="welcome">
  <h2 class="section-title" style="top:68px">Welcome to Quillmere Imports</h2>
  <p class="lead">Proin placerat dapibus gravida. In tristique tristique nulla eget hendrerit. Maecenas vel tortor accumsan quam varius imperdiet vel eget elit. Aenean facilisis tincidunt lectus, id dictum nisi luctus eget. Vivamus efficitur ex condimentum, malesuada eros eget, feugiat nibh. Sed tellus ex, imperdiet eget gravida sit amet, volutpat eget turpis. In nec ultricies est. Etiam mattis augue vehicula odio posuere, sit amet tempus lectus luctus.</p>
  <ul class="bullets" style="left:133px">
    <li>Duis hendrerit arcu ut sem egestas, vulputate porttitor</li>
    <li>Pellentesque vehicula nulla molestie lectus</li>
    <li>Integer ac est euismod, posuere diam et, scelerisque vulputate</li>
    <li>Nam elementum velit nec</li>
  </ul>
  <ul class="bullets" style="left:619px">
    <li>Maecenas sed nibh sed nisi tristique pharetra</li>
    <li>Vestibulum ut velit elementum, bibendum neque in, mollis quam</li>
    <li>Quisque blandit elit at urna tincidunt</li>
    <li>Duis id quam auctor, dapibus justo commodo</li>
  </ul>
  <div class="btn" style="left:547px;top:342px;width:106px;height:41px">Read more</div>
</section>

<section class="services" role="img" aria-label="Darkened photo of stacked shipping containers at a port">
  <h2 class="section-title">Our Services</h2>
  <div class="service-card" style="left:133px">
    <svg width="84" height="60" viewBox="0 0 84 60" fill="none" stroke="#fff" stroke-width="2.5"><rect x="3" y="6" width="50" height="36"/><path d="M53 18h16l11 12v12H53z"/><circle cx="18" cy="47" r="6" fill="#3a3a3a"/><circle cx="66" cy="47" r="6" fill="#3a3a3a"/><path d="M13 12v24M23 12v24M33 12v24M43 12v24"/></svg>
    <h3>Road Services</h3>
    <p>Aliquam erat volutpat. Quisque aliquet ex nec est vestibulum pulvinar. Pellentesque convallis molestie enim sit amet efficitur.</p>
    <div class="btn">Read more</div>
  </div>
  <div class="service-card" style="left:449px">
    <svg width="84" height="60" viewBox="0 0 84 60" fill="none" stroke="#fff" stroke-width="2.5"><path d="M40 2v8M30 10h20v12H30zM20 22h40v12H20zM10 34h64l-8 14H18z"/><path d="M6 54c6-4 10 4 16 0s10 4 16 0 10 4 16 0 10 4 16 0 10 4 12 0"/></svg>
    <h3>Sea Services</h3>
    <p>Aliquam erat volutpat. Quisque aliquet ex nec est vestibulum pulvinar. Pellentesque convallis molestie enim sit amet efficitur.</p>
    <div class="btn">Read more</div>
  </div>
  <div class="service-card" style="left:768px">
    <svg width="84" height="60" viewBox="0 0 84 60" fill="#fff"><path d="M39 4c0-3 6-3 6 0v18l30 14v6L45 34v14l8 6v4l-11-3-11 3v-4l8-6V34L9 42v-6l30-14z"/></svg>
    <h3>Flight Services</h3>
    <p>Aliquam erat volutpat. Quisque aliquet ex nec est vestibulum pulvinar. Pellentesque convallis molestie enim sit amet efficitur.</p>
    <div class="btn">Read more</div>
  </div>
</section>

<section class="cases">
  <h2 class="section-title" style="top:70px">Case Studies</h2>
  <svg class="arrow" style="left:46px" width="16" height="28" viewBox="0 0 16 28"><path d="M13 3L4 14l9 11" stroke="#999" stroke-width="3" fill="none"/></svg>
  <svg class="arrow" style="left:1130px" width="16" height="28" viewBox="0 0 16 28"><path d="M3 3l9 11-9 11" stroke="#999" stroke-width="3" fill="none"/></svg>
  <article class="case" style="left:133px">
    <div class="photo" role="img" aria-label="Photo of a bright warehouse with tall pallet racks" style="background:linear-gradient(180deg,#c9ced6,#8c94a0 60%,#d7dbe0)"></div>
    <h4>Quisque aliquet ex nec est vestibulum pulvinar.</h4>
    <p>Vestibulum condimentum, risus posuere cursus, Pellentesque a imperdiet dolor, et auctor. Fusce sollicitudin lorem et luctus volutpat. Proin placerat dapibus gravida.</p>
    <div class="btn">Read more</div>
  </article>
  <article class="case" style="left:449px">
    <div class="photo" role="img" aria-label="Photo of colourful shipping containers stacked at a port" style="background:linear-gradient(135deg,#3f6c8f,#b84a3a 45%,#5d8aa8 75%,#c9a078)"></div>
    <h4>Quisque aliquet ex nec est vestibulum pulvinar.</h4>
    <p>Vestibulum condimentum, risus posuere cursus, Pellentesque a imperdiet dolor, et auctor. Fusce sollicitudin lorem et luctus volutpat. Proin placerat dapibus gravida.</p>
    <div class="btn">Read more</div>
  </article>
  <article class="case" style="left:768px">
    <div class="photo" role="img" aria-label="Photo of a freight train at sunset with a plane overhead" style="background:linear-gradient(160deg,#3a2a22,#c8742e 45%,#6a3d22 75%,#2a1d18)"></div>
    <h4>Quisque aliquet ex nec est vestibulum pulvinar.</h4>
    <p>Vestibulum condimentum, risus posuere cursus, Pellentesque a imperdiet dolor, et auctor. Fusce sollicitudin lorem et luctus volutpat. Proin placerat dapibus gravida.</p>
    <div class="btn">Read more</div>
  </article>
</section>

<section class="contact">
  <h2 class="section-title" style="top:75px">Contact Us</h2>
  <div class="field" style="left:133px;top:130px;width:217px">Name</div>
  <div class="field" style="left:371px;top:130px;width:217px">Phone Number</div>
  <div class="field" style="left:610px;top:130px;width:218px">Email Address</div>
  <div class="field" style="left:848px;top:130px;width:219px;justify-content:space-between">Service for<svg width="10" height="6" viewBox="0 0 10 6"><path d="M0 0h10L5 6z" fill="#333"/></svg></div>
  <div class="field" style="left:133px;top:195px;width:934px">Message</div>
  <div class="btn" style="left:559px;top:257px;width:82px;height:33px;font-size:11px">Submit</div>
</section>

<footer class="site-footer">
  <div class="footer-brand">QUILLMERE IMPORTS</div>
  <div class="fcol" style="left:133px"><h5>About Us</h5>Our History<br>Our Team<br>Why Us?</div>
  <div class="fcol" style="left:254px"><h5>Services</h5>Road Services<br>Sea Services<br>Flight Services</div>
  <div class="fcol" style="left:389px"><h5>Case Studies</h5>Vivamus eleifend<br>Etiam imperdiet<br>Vivamus lacus<br>Fusce vitae</div>
  <div class="fcol" style="left:549px"><h5>Contact Info</h5>24 Building name, Street name, City Zipcode<br>Phone : 555 210 4387<br>Fax : 555 210 4390<br>Email : info@quillmereimports.com</div>
  <div class="fcol" style="left:827px"><h5>More Links</h5>Aliquam ac elit vitae sapien elementum<br>Nulla ut neque mattis, ornare ipsum pellentesque<br>Nam ultrices orci nec odio tincidunt dignissim<br>Proin ut enim blandit</div>
  <div class="footer-rule"></div>
  <div class="legal">Copyright © 2108 Quillmere Imports. All rights reserved. &nbsp; Sitemap &nbsp;|&nbsp; Privacy Policy &nbsp;|&nbsp; Terms and Conditions</div>
  <div class="social"><span></span><span></span><span></span><span></span></div>
</footer>

</body>
</html>
```